Need App for Impact Related Events

My app is to help with internal events. When you enter the prompted event code the next screen shows you everyone currently at the event. It will give you the ability to Start a conversation with someone you met at that event, or signal it is your turn to send a message. The next screen is a message thread with that person. I am looking for a design that incorporates the colors and ‘feel good’ emotion of our logo. I have pieced together a pretty good interpretation of what I’m looking for in the attached mockup by slicing and dicing designs. I also attached our logo mascot.Screens (see attached mockups)

Note 1: I do not like the picture on the screen used in screen one because it makes it seem like a dating app. I attached an alternative photo that can be used or present different ideas.

Note 2: On the login/signup screen (screen 2) I need an additional first and last name for login, you can try to fit this on one login screen or present a two step signup screen where that is presented in the second screen.

READ MOCKUP GUIDELINES UNDER Must Haves

Target Market(s)

People attending internal social impact events

Industry/Entity Type

Charity

Font styles to use
Sans Serif

Colors
86cfc6

Requirements
Must have
• Follow the screen mockups attached to project
• PLEASE READ
• I have provided a relatively close design of what I’m looking for in the mockups. Some screens need to be followed more closely to my design mockup than other. I have listed a guide below how how closely you should follow my mockup design exactly. Overall I would like to see some ideas of incorporating a few accent colors so it doesn’t appear SO Blue. I also attached some app inspiration designs I found from around the web
• Screen Mockup Guideline Follow %
• Screen 1: 65% - mostly on target, would like to see ways to make it not SO Blue and possibly creative places to add some explainer text describing the app
• Screen 2: 50% - general design idea is here, but more open
• Screen 3: 35% - a lot more room for design influence
• Screen 4: 70% - mostly on target, a little room for design influence/color scheme ideas
• Screen 5-6: 25% - a lot of room for design change/ideas/influence
• Screen 7-8: 80% - already very close to what I need, maybe open to slight sizing and color scheme ideas
• Screen 9: 15% - the most open for influence, only the general functionality of the screen is communicated here
Nice to have
• Please Read Mockup Guideline above. In large part I am looking for something to use some nice accent colors so it is not overwhelmingly blue and bring the whole design into a seamless style.
Should not have

```html
<!DOCTYPE html>
<html lang="en">
<head>
<meta charset="utf-8">
<title>Sign up</title>
<link href="https://fonts.googleapis.com/css2?family=Montserrat:wght@400;500;600;700&family=Inter:wght@400;500;600&display=swap" rel="stylesheet">
<style>
  :root {
    --white: #ffffff;
    --navy: #1d3a5c;
    --brand: #86cfc6;
    --brand-deep: #4fb3a7;
    --accent: #f4845f;
    --accent-soft: #ffd37a;
    --muted: #a3abb6;
    --rule: #dfe3e8;
    --social-start: #2b78b7;
    --social-end: #52b7e2;
    --kbd-bg: #d2d5db;
    --key: #ffffff;
    --key-dark: #abb1ba;
    --key-text: #111111;
    --key-shadow: #888b90;
  }
  * { box-sizing: border-box; margin: 0; padding: 0; }
  html, body { width: 675px; height: 1200px; overflow: hidden; background: var(--white); }
  body { position: relative; font-family: "Montserrat", Arial, sans-serif; color: var(--navy); }

  .status-bar { position: absolute; top: 0; left: 0; width: 675px; height: 38px; font-family: "Inter", Arial, sans-serif; font-size: 22px; color: #000; }
  .status-bar .carrier { position: absolute; left: 10px; top: 6px; display: flex; align-items: center; gap: 8px; }
  .status-bar .dots { display: flex; gap: 3px; }
  .status-bar .dots i { width: 9px; height: 9px; border-radius: 50%; background: #000; display: block; }
  .status-bar .time { position: absolute; left: 0; right: 0; top: 6px; text-align: center; font-weight: 600; }
  .status-bar .power { position: absolute; right: 10px; top: 6px; display: flex; align-items: center; gap: 8px; }
  .battery { width: 44px; height: 20px; border: 2px solid #000; border-radius: 5px; padding: 2px; position: relative; }
  .battery::after { content: ""; position: absolute; right: -6px; top: 5px; width: 3px; height: 7px; background: #000; border-radius: 0 2px 2px 0; }
  .battery span { display: block; width: 100%; height: 100%; background: #000; border-radius: 2px; }

  .nav { position: absolute; top: 38px; left: 0; width: 675px; height: 70px; }
  .nav .back { position: absolute; left: 18px; top: 20px; }
  .nav .title { position: absolute; left: 0; right: 0; top: 18px; text-align: center; font-size: 27px; font-weight: 700; }

  .btn { position: absolute; display: flex; align-items: center; justify-content: center; gap: 18px; color: var(--white); font-size: 26px; font-weight: 500; border-radius: 60px; }
  .btn b { font-weight: 700; }
  .btn-social { left: 38px; top: 128px; width: 596px; height: 90px; background: linear-gradient(90deg, var(--social-start), var(--social-end)); }
  .btn-social .mark { width: 24px; height: 24px; background: var(--white); border-radius: 3px; }
  .btn-email { left: 22px; top: 650px; width: 633px; height: 96px; background: linear-gradient(90deg, var(--brand-deep), var(--brand)); box-shadow: 0 6px 0 var(--accent-soft); }

  .divider { position: absolute; top: 246px; left: 36px; width: 603px; display: flex; align-items: center; gap: 22px; font-size: 23px; }
  .divider::before, .divider::after { content: ""; flex: 1; height: 2px; background: var(--rule); }
  .divider b { font-weight: 700; color: var(--accent); }

  .field { position: absolute; border-bottom: 2px solid var(--rule); }
  .field label { display: block; font-size: 22px; font-weight: 700; line-height: 27px; }
  .field .placeholder { display: block; margin-top: 14px; padding-bottom: 12px; font-size: 29px; line-height: 36px; color: var(--muted); position: relative; white-space: nowrap; }
  .field-first { top: 296px; left: 34px; width: 288px; }
  .field-last { top: 296px; left: 352px; width: 288px; }
  .field-email { top: 414px; left: 34px; width: 606px; border-bottom-color: var(--accent); }
  .field-email .placeholder::before { content: ""; position: absolute; left: -2px; top: 0; width: 3px; height: 36px; background: var(--accent); }
  .field-password { top: 532px; left: 34px; width: 606px; }

  .keyboard { position: absolute; left: 0; top: 812px; width: 675px; height: 388px; background: var(--kbd-bg); font-family: "Inter", Arial, sans-serif; }
  .kbd-row { position: absolute; left: 0; width: 675px; display: flex; gap: 10.8px; padding: 0 7px; }
  .row-1 { top: 20px; }
  .row-2 { top: 117px; justify-content: center; }
  .row-3 { top: 214px; justify-content: space-between; }
  .row-4 { top: 308px; }
  .kbd-row .group { display: flex; gap: 10.8px; }
  .key { width: 57.6px; height: 76px; background: var(--key); border-radius: 9px; box-shadow: 0 2px 0 var(--key-shadow); display: flex; align-items: center; justify-content: center; font-size: 40px; color: var(--key-text); }
  .key.dark { background: var(--key-dark); }
  .key.wide { width: 76px; }
  .key.label { font-size: 26px; }
  .key-123 { width: 79px; }
  .key-emoji { width: 68px; }
  .key-mic { width: 56px; }
  .key-space { flex: 1; }
  .key-return { width: 151px; }
</style>
</head>
<body>
  <div class="status-bar">
    <div class="carrier">
      <span class="dots"><i></i><i></i><i></i><i></i><i></i></span>
      <span>Nimbus</span>
      <svg width="26" height="20" viewBox="0 0 26 20"><path d="M13 19 L2 7 A16 16 0 0 1 24 7 Z" fill="#000"/></svg>
    </div>
    <div class="time">9:41 AM</div>
    <div class="power">
      <svg width="14" height="22" viewBox="0 0 14 22"><path d="M2 6 L12 15 L7 20 V2 L12 7 L2 16" fill="none" stroke="#000" stroke-width="2"/></svg>
      <span>100%</span>
      <span class="battery"><span></span></span>
    </div>
  </div>

  <header class="nav">
    <svg class="back" width="20" height="34" viewBox="0 0 20 34"><path d="M17 3 L4 17 L17 31" fill="none" stroke="var(--accent)" stroke-width="3.5" stroke-linecap="round" stroke-linejoin="round"/></svg>
    <h1 class="title">Sign up</h1>
  </header>

  <div class="btn btn-social"><span class="mark"></span><span>Start with <b>Circlebook</b></span></div>

  <div class="divider"><span><b>Or</b>, start with email</span></div>

  <div class="field field-first">
    <label>First name</label>
    <span class="placeholder">Jane</span>
  </div>
  <div class="field field-last">
    <label>Last name</label>
    <span class="placeholder">Doe</span>
  </div>
  <div class="field field-email">
    <label>Email address</label>
    <span class="placeholder">example@yourmail.com</span>
  </div>
  <div class="field field-password">
    <label>Password</label>
    <span class="placeholder">Create a password (6+ characters)</span>
  </div>

  <div class="btn btn-email">
    <svg width="32" height="24" viewBox="0 0 32 24"><rect x="1.5" y="1.5" width="29" height="21" fill="none" stroke="#fff" stroke-width="2.4"/><path d="M2 3 L16 13 L30 3" fill="none" stroke="#fff" stroke-width="2.4"/></svg>
    <span>Continue with <b>email</b></span>
  </div>

  <div class="keyboard">
    <div class="kbd-row row-1">
      <span class="key">q</span><span class="key">w</span><span class="key">e</span><span class="key">r</span><span class="key">t</span><span class="key">y</span><span class="key">u</span><span class="key">i</span><span class="key">o</span><span class="key">p</span>
    </div>
    <div class="kbd-row row-2">
      <span class="key">a</span><span class="key">s</span><span class="key">d</span><span class="key">f</span><span class="key">g</span><span class="key">h</span><span class="key">j</span><span class="key">k</span><span class="key">l</span>
    </div>
    <div class="kbd-row row-3">
      <span class="key dark wide"><svg width="32" height="30" viewBox="0 0 32 30"><path d="M16 3 L29 16 H22 V27 H10 V16 H3 Z" fill="none" stroke="#222" stroke-width="2.4" stroke-linejoin="round"/></svg></span>
      <span class="group">
        <span class="key">z</span><span class="key">x</span><span class="key">c</span><span class="key">v</span><span class="key">b</span><span class="key">n</span><span class="key">m</span>
      </span>
      <span class="key dark wide"><svg width="40" height="28" viewBox="0 0 40 28"><path d="M12 2 H37 V26 H12 L2 14 Z" fill="none" stroke="#222" stroke-width="2.4" stroke-linejoin="round"/><path d="M19 8 L29 20 M29 8 L19 20" stroke="#222" stroke-width="2.4"/></svg></span>
    </div>
    <div class="kbd-row row-4">
      <span class="key dark label key-123">123</span>
      <span class="key dark key-emoji"><svg width="34" height="34" viewBox="0 0 34 34"><circle cx="17" cy="17" r="14" fill="none" stroke="#222" stroke-width="2.4"/><circle cx="12" cy="13" r="2" fill="#222"/><circle cx="22" cy="13" r="2" fill="#222"/><path d="M10 20 Q17 27 24 20" fill="none" stroke="#222" stroke-width="2.4"/></svg></span>
      <span class="key key-mic"><svg width="22" height="36" viewBox="0 0 22 36"><rect x="6" y="2" width="10" height="20" rx="5" fill="none" stroke="#222" stroke-width="2.4"/><path d="M2 16 Q2 28 11 28 Q20 28 20 16 M11 28 V34" fill="none" stroke="#222" stroke-width="2.4"/></svg></span>
      <span class="key label key-space">space</span>
      <span class="key dark label key-return">return</span>
    </div>
  </div>
</body>
</html>
```